Business Card Design

Business Card for professional consulting firm working with large financial institutions.

Target Market(s)

Executive buyers

Industry/Entity Type

Banking

Contact Information for Business Card

Mild creativity wanted. Not boring, but do elaborate artwork.

Font styles to use
Serif
Sans Serif

Colors

Designer to choose colors to be used in the design.

Requirements
Must have
• Standard business card features - company name, individual name, telephone, website, email, locations.
Nice to have
• Two colors
Should not have
• too many colors, fancy printing, cartoons.

```html
<!DOCTYPE html>
<html lang="en">
<head>
<meta charset="utf-8">
<title>Veritan Partners – Business Card</title>
<link rel="stylesheet" href="https://fonts.googleapis.com/css2?family=Roboto:wght@400&family=Roboto+Slab:wght@400;700&display=swap">
<style>
  :root {
    --backdrop: #e4e4e3;
    --card-white: #f4f4f3;
    --card-black: #1a1a1a;
    --ink: #111111;
    --ink-soft: #4a4a4a;
    --ink-muted: #9a9a9a;
    --band-grey: #a8a8a8;
    --mark-white: #f2f2f2;
  }
  * { margin: 0; padding: 0; box-sizing: border-box; }
  html, body {
    width: 1200px; height: 960px; overflow: hidden;
    background: var(--backdrop);
  }
  .canvas { position: relative; width: 1200px; height: 960px; }

  .card { position: absolute; width: 602px; height: 342px; overflow: hidden; }
  .card-front { left: 314px; top: 113px; background: var(--card-white); }
  .card-back { left: 311px; top: 472px; width: 600px; height: 343px; background: var(--card-black); }

  .company-name {
    position: absolute; left: 66px; top: 72px;
    font-family: "Roboto Slab", serif; font-weight: 400;
    font-size: 27px; color: var(--ink-soft); letter-spacing: 0.2px;
  }

  .person { position: absolute; left: 69px; top: 216px; }
  .person-name {
    font-family: "Roboto Slab", serif; font-weight: 700;
    font-size: 21px; color: var(--ink); letter-spacing: 0.5px; line-height: 1;
  }
  .person-title {
    margin-top: 5px;
    font-family: "Roboto Slab", serif; font-weight: 400;
    font-size: 14px; color: var(--ink-muted); letter-spacing: 0.4px;
  }

  .contact {
    position: absolute; left: 345px; top: 187px;
    font-family: "Roboto", sans-serif; font-size: 14.5px; color: var(--ink-soft);
    line-height: 18.5px;
  }
  .contact-address { margin-bottom: 11px; }
  .contact-line { display: flex; align-items: center; gap: 7px; }
  .contact-line svg { width: 13px; height: 13px; flex: none; fill: var(--ink); }

  .bottom-band {
    position: absolute; left: 0; bottom: 0; width: 100%; height: 9px;
    background: var(--band-grey);
  }
  .bottom-tab {
    position: absolute; left: 66px; bottom: 0; width: 141px; height: 18px;
    background: var(--ink);
  }

  .back-mark {
    position: absolute; right: 62px; bottom: 44px;
    font-family: "Roboto Slab", serif; font-weight: 400;
    font-size: 52px; color: var(--mark-white); line-height: 1;
  }
</style>
</head>
<body>
<main class="canvas">
  <section class="card card-front" aria-label="Business card front">
    <div class="company-name">Veritan Partners</div>

    <div class="person">
      <div class="person-name">DANIEL HARLOW</div>
      <div class="person-title">CEO/FOUNDER</div>
    </div>

    <div class="contact">
      <div class="contact-address">2140 Birchwood Court<br>Juneau, Alaska 99801</div>
      <div class="contact-line">
        <svg viewBox="0 0 16 16" aria-hidden="true"><path d="M3.6 1.2l2.3 2.6-1.2 2c.9 2 2.5 3.6 4.5 4.5l2-1.2 2.6 2.3-1.3 2.4C7 13.6 2.4 9 1.2 2.5z"/></svg>
        <span>555 210 4876</span>
      </div>
      <div class="contact-line">
        <svg viewBox="0 0 16 16" aria-hidden="true"><path d="M1 3.5h14v9H1z M1.8 4.3L8 9l6.2-4.7" stroke="#f4f4f3" stroke-width="1.2"/></svg>
        <span>info@veritanpartners.com</span>
      </div>
      <div class="contact-line">
        <svg viewBox="0 0 16 16" aria-hidden="true"><circle cx="8" cy="8" r="7"/><path d="M1 8h14M8 1c-2.5 2.5-2.5 11.5 0 14M8 1c2.5 2.5 2.5 11.5 0 14" stroke="#f4f4f3" stroke-width="1" fill="none"/></svg>
        <span>www.veritanpartners.com</span>
      </div>
    </div>

    <div class="bottom-band"></div>
    <div class="bottom-tab"></div>
  </section>

  <section class="card card-back" aria-label="Business card back">
    <div class="back-mark">veritan</div>
  </section>
</main>
</body>
</html>
```